Business card for Crestline Bathrooms

Please design a business card for our bathroom renovation business. You can use my existing logo, but if you have an idea to modernize it, I would like to see it. Please see attached files first. I would like to use the blue and the orange theme. I like the concept of using the shower head in the logo. Please find following a design (or two) that I have been trying to create with my limited resources. That design was for a sign, but I was going to adopt it and use it as a business card as well. I like the concept of the water splash but I don’t think it “flows” nicely together with the logo. Another thought is that maybe creating the logo out of water splash could work and have a dramatic effect (like the water text and the butterfly picture attached with similar background instead of white). If the above doesn’t work I would like to see a modern simplified design. One of the attached files named as the unwanted business card has all the details that I want included in the business card. Please note that it is two sided.
Updates

I am very thankful for the designs that I have received, but they are very similar and only a couple of attempts to do something with the water splash as per my original brief. Modernizing the logo and having it made out of out of water splash with the orange as color accent could work and have a dramatic effect (like the water text and the butterfly picture attached with similar background instead of white). Please do not use the butterfly itself! This is just an example that images can be created out of water splash.

Contact Information for Business Card

all the details are on the unwonted business card file included

Colors
3176b5

Requirements
Nice to have
• Copied from the brief:
• ... maybe creating the logo out of water splash could work and have a dramatic effect (like the water text and the butterfly picture attached with similar background instead of white). Please do not use the butterfly itself!
Should not have
• I am getting designs with a butterfly. The butterfly picture was an example of creating something from a water splash. The butterfly itself has no association with anything other than the concept of creating a logo out of water splash. Sorry, I thought I was clear in the brief.

```html
<!DOCTYPE html>
<html lang="en">
<head>
<meta charset="utf-8">
<title>Crestline Bathrooms – Business Card</title>
<link rel="stylesheet" href="https://fonts.googleapis.com/css2?family=Patrick+Hand&family=Roboto:wght@400;500&family=Roboto+Condensed:wght@400&display=swap">
<style>
  :root {
    --backdrop: #e8e8e8;
    --navy: #1a2f50;
    --navy-deep: #152744;
    --splash-light: #5b84b3;
    --splash-mid: #2c5283;
    --coral: #e8735f;
    --white: #ffffff;
  }
  * { box-sizing: border-box; margin: 0; padding: 0; }
  html, body {
    width: 1200px; height: 960px; overflow: hidden;
    background: var(--backdrop);
  }
  .stage { position: relative; width: 1200px; height: 960px; }

  .card {
    position: absolute;
    width: 600px; height: 343px;
    background: var(--navy);
    overflow: hidden;
    box-shadow: 2px 3px 6px rgba(0,0,0,0.25);
  }
  .card--front { left: 302px; top: 124px; }
  .card--back  { left: 299px; top: 493px; }

  /* front */
  .splash-photo {
    position: absolute; left: 0; top: 0; width: 290px; height: 343px;
    background:
      radial-gradient(ellipse 160px 90px at 190px 310px, rgba(220,232,245,0.55), transparent 70%),
      radial-gradient(ellipse 120px 170px at 40px 200px, rgba(160,190,225,0.45), transparent 75%),
      linear-gradient(90deg, var(--splash-mid) 0%, var(--splash-mid) 35%, var(--navy) 100%);
  }
  .holder-name {
    position: absolute; left: 299px; top: 92px;
    font-family: "Patrick Hand", cursive;
    font-size: 29px; color: var(--coral); letter-spacing: 0.5px;
  }
  .contact-list { position: absolute; left: 299px; top: 138px; list-style: none; }
  .contact-list li {
    display: flex; align-items: center; height: 20px;
    font-family: "Roboto", sans-serif; font-size: 14.5px; color: var(--white);
  }
  .contact-list svg { width: 14px; height: 14px; margin-right: 11px; fill: var(--coral); flex: none; }

  /* back */
  .brand {
    position: absolute; left: 48px; top: 96px;
    display: flex; align-items: center; gap: 12px;
  }
  .brand-dot { width: 18px; height: 18px; border-radius: 50%; background: var(--coral); flex: none; }
  .brand-name {
    font-family: "Roboto", sans-serif; font-weight: 500;
    font-size: 27px; line-height: 1.15; color: var(--white);
  }
  .services { position: absolute; left: 259px; top: 134px; list-style: none; }
  .services li {
    position: relative; padding-left: 13px; height: 20px;
    font-family: "Roboto Condensed", sans-serif; font-size: 14.5px; color: var(--white);
  }
  .services li::before {
    content: ""; position: absolute; left: 0; top: 6px;
    width: 5px; height: 5px; border-radius: 50%; background: var(--coral);
  }
  .memberships { position: absolute; left: 406px; top: 290px; display: flex; align-items: center; gap: 10px; }
  .badge-round { width: 24px; height: 26px; border-radius: 6px; background: var(--white); }
  .badge-divider { width: 1px; height: 24px; background: var(--white); }
  .badge-wide { width: 118px; height: 22px; border-radius: 2px; background: var(--white); }
</style>
</head>
<body>
<main class="stage">

  <section class="card card--front">
    <div class="splash-photo" role="img" aria-label="Photo of water droplets and a splash on a deep blue background"></div>
    <h1 class="holder-name">Daniel Marsh</h1>
    <ul class="contact-list">
      <li><svg viewBox="0 0 14 14"><path d="M4 0h6a1 1 0 0 1 1 1v12a1 1 0 0 1-1 1H4a1 1 0 0 1-1-1V1a1 1 0 0 1 1-1zm.5 1.5v9h5v-9zM7 11.3a.8.8 0 1 0 0 1.6.8.8 0 0 0 0-1.6z"/></svg>6200 4187</li>
      <li><svg viewBox="0 0 14 14"><path d="M3 .5l2.3 2.9-1.2 1.8c.9 1.9 2.5 3.5 4.6 4.6l1.8-1.2 2.9 2.3-1.4 2.4C6.5 13 1 7.6.8 2z"/></svg>0400 318 902</li>
      <li><svg viewBox="0 0 14 14"><path d="M1 3h12v8H1zm1 .9v.3l5 3.3 5-3.3v-.3z"/></svg>daniel@crestlinebathrooms.com.au</li>
      <li><svg viewBox="0 0 14 14"><path d="M7 .5a6.5 6.5 0 1 0 0 13 6.5 6.5 0 0 0 0-13zM3 4.5c1 0 2 .8 2 1.8s1.3 1 1.3 2.2S5 10.3 5 11.7A5 5 0 0 1 3 4.5zm5.2-2.4c-.3.9.5 1.5 1.4 1.6.9.1 1.1 1.4.5 2.1-.6.6.5 1.6 1.5 1.2.4 0 .7-.3.9-.6a5 5 0 0 1-1.9 4.2c-.6-1-1.8-1.4-1.3-2.6.4-.9-1-1.3-1.9-1.7C6.5 5.9 7 4.6 6.6 3.6 6.3 2.9 7 2.2 8.2 2.1z"/></svg>www.crestlinebathrooms.com.au</li>
      <li><svg viewBox="0 0 14 14"><path d="M7 0a4.8 4.8 0 0 0-4.8 4.8C2.2 8.5 7 14 7 14s4.8-5.5 4.8-9.2A4.8 4.8 0 0 0 7 0zm0 3a1.8 1.8 0 1 1 0 3.6A1.8 1.8 0 0 1 7 3z"/></svg>PO Box 48, Hillview 2600</li>
    </ul>
  </section>

  <section class="card card--back">
    <div class="brand">
      <span class="brand-dot"></span>
      <span class="brand-name">Crestline<br>Bathrooms</span>
    </div>
    <ul class="services">
      <li>Complete Bathroom Renovations &amp; Remodelling</li>
      <li>Highly Skilled &amp; Qualified Tradespeople</li>
      <li>Professional Service From Concept To Completion</li>
      <li>All Work Guaranteed</li>
    </ul>
    <div class="memberships" aria-label="Industry membership badges">
      <span class="badge-round"></span>
      <span class="badge-divider"></span>
      <span class="badge-wide"></span>
    </div>
  </section>

</main>
</body>
</html>
```